business card Calvanto

Wee need a business card design for a new compagny based on Paris
We developped innovative a platform for selling services to refresh, beautify and develop its housing.
We would like a red logo on a black background
Te final design should communicate quality service, know-how, high-end

Target Market(s)

individuals

Industry/Entity Type

Business

```html
<!DOCTYPE html>
<html lang="en">
<head>
<meta charset="utf-8">
<title>Calvanto business card</title>
<link rel="stylesheet" href="https://fonts.googleapis.com/css2?family=Poppins:wght@300;400&family=Montserrat:wght@500;600&display=swap">
<style>
  :root {
    --backdrop: #e4e4e4;
    --card-black: #0b0b0d;
    --card-sheen: #2a2a2e;
    --coral: #e8706a;
    --coral-dark: #d95f59;
    --wordmark-grey: #a8a8aa;
    --detail-white: #e9e9e9;
    --stripe: rgba(255,255,255,0.035);
  }
  * { margin: 0; padding: 0; box-sizing: border-box; }
  html, body {
    width: 1200px; height: 852px; overflow: hidden;
    background: var(--backdrop);
  }
  .canvas { position: relative; width: 1200px; height: 852px; }

  .card {
    position: absolute;
    width: 520px; height: 300px;
    border-radius: 26px;
    background: var(--card-black);
    overflow: hidden;
    box-shadow: 0 6px 14px rgba(0,0,0,0.25);
  }
  .card-front {
    left: 60px; top: 150px;
    background:
      linear-gradient(115deg, transparent 38%, rgba(255,255,255,0.07) 48%, transparent 60%),
      radial-gradient(ellipse at 70% 30%, var(--card-sheen) 0%, var(--card-black) 60%);
  }
  .card-back {
    left: 620px; top: 400px;
    background:
      linear-gradient(115deg, transparent 30%, rgba(255,255,255,0.06) 40%, transparent 52%),
      repeating-linear-gradient(90deg, var(--stripe) 0 2px, transparent 2px 12px),
      var(--card-black);
  }

  .brand {
    position: absolute;
    display: flex; align-items: center; gap: 14px;
  }
  .brand-square {
    width: 52px; height: 52px;
    background: var(--coral);
  }
  .brand-name {
    font-family: "Poppins", sans-serif;
    font-weight: 300;
    font-size: 46px;
    line-height: 1;
    color: var(--wordmark-grey);
    letter-spacing: 0.5px;
  }
  .card-front .brand { left: 50%; top: 50%; transform: translate(-50%, -50%); }
  .card-back .brand { left: 200px; top: 56px; }
  .card-back .brand-square { width: 44px; height: 44px; }
  .card-back .brand-name { font-size: 38px; }

  .address {
    position: absolute; right: 28px; top: 138px;
    display: flex; align-items: center; gap: 14px;
    font-family: "Montserrat", sans-serif; font-weight: 500;
    font-size: 12px; line-height: 1.5; color: var(--detail-white);
    text-align: right;
  }
  .address svg { width: 12px; height: 16px; fill: var(--coral); }

  .name-tab {
    position: absolute; left: 0; top: 182px;
    width: 230px; height: 42px;
    background: var(--coral);
    border-radius: 0 10px 10px 0;
    display: flex; align-items: center; padding-left: 36px;
    font-family: "Montserrat", sans-serif; font-weight: 600;
    font-size: 17px; letter-spacing: 1.5px; color: #1a1a1a;
  }

  .contacts {
    position: absolute; left: 28px; top: 236px;
    list-style: none;
    font-family: "Montserrat", sans-serif; font-weight: 500;
    font-size: 12px; color: var(--detail-white);
  }
  .contacts li { display: flex; align-items: center; gap: 10px; height: 18px; }
  .contacts svg { width: 12px; height: 12px; fill: var(--coral); stroke: var(--coral); }
</style>
</head>
<body>
<main class="canvas">

  <section class="card card-front" aria-label="Card front">
    <div class="brand">
      <span class="brand-square"></span>
      <span class="brand-name">Calvanto</span>
    </div>
  </section>

  <section class="card card-back" aria-label="Card back">
    <div class="brand">
      <span class="brand-square"></span>
      <span class="brand-name">Calvanto</span>
    </div>

    <div class="address">
      <svg viewBox="0 0 12 16" aria-hidden="true"><path d="M6 0a6 6 0 0 0-6 6c0 4.5 6 10 6 10s6-5.5 6-10a6 6 0 0 0-6-6zm0 8.5A2.5 2.5 0 1 1 6 3.5a2.5 2.5 0 0 1 0 5z"/></svg>
      <p>xyz, Streeno. 6, New<br>Street, your Colony, NZ</p>
    </div>

    <div class="name-tab">YOUR NAME</div>

    <ul class="contacts">
      <li>
        <svg viewBox="0 0 12 12" aria-hidden="true"><path stroke="none" d="M2.5 0.5l2 2.2-1 1.3c.8 1.6 2 2.8 3.5 3.5l1.3-1 2.2 2-1.2 2C5 10.5 1.5 7 0.5 1.7z"/></svg>
        <span>+00 000 000 000</span>
      </li>
      <li>
        <svg viewBox="0 0 12 12" aria-hidden="true"><path stroke="none" d="M0 2h12v8H0z"/><path fill="none" stroke="#0b0b0d" stroke-width="1.2" d="M0.5 2.5L6 7l5.5-4.5"/></svg>
        <span>yourname@yourwebsite.com</span>
      </li>
      <li>
        <svg viewBox="0 0 12 12" aria-hidden="true"><g fill="none" stroke-width="1.1"><circle cx="6" cy="6" r="5.3"/><ellipse cx="6" cy="6" rx="2.3" ry="5.3"/><path d="M0.7 6h10.6M1.6 3.3h8.8M1.6 8.7h8.8"/></g></svg>
        <span>www.yourwebsite.com</span>
      </li>
    </ul>
  </section>

</main>
</body>
</html>
```